Verodex business card

Business card for sustainable investment company called "Verodex". Verodex is an exchange platform selling carbon credits between buyers and sellers. Carbon Credits are an environmental commodity for reducing global carbon emissions.

the card should obviously have our logo and the theme should be sustainability/environment mixed with a trading platform.

Contact Information for Business Card

Logo, Name, Title, Phone, Email

Colors
0054AA
0677BA
7BADD7
CADEEF
E8F1F8
0094D4
00A9DD
6FCCEA
C7EBF8
E9F6FB
00AB8E
00BBA5
67D7C9
C6EFE9
E9F9F6
59FF00
82FF00
B8FF75
E3FFCB
F4FFEA

```html
<!DOCTYPE html>
<html lang="en">
<head>
<meta charset="utf-8">
<title>Verodex Business Card</title>
<link rel="stylesheet" href="https://fonts.googleapis.com/css2?family=Poppins:wght@400;500;600&display=swap">
<style>
  :root {
    --page-bg: #e6e6e6;
    --card-white: #f7f7f8;
    --navy: #253a5a;
    --ink: #1d2533;
    --cyan: #22b8e4;
    --brand-blue: #2a86e0;
    --back-top: #14365f;
    --back-bottom: #0b2a55;
    --rule: #2b2f36;
  }
  * { margin: 0; padding: 0; box-sizing: border-box; }
  html, body {
    width: 1200px; height: 1200px; overflow: hidden;
    background: var(--page-bg);
    font-family: "Poppins", sans-serif;
  }
  .card {
    position: absolute;
    left: 262px;
    width: 686px;
    height: 392px;
    border-radius: 22px;
    overflow: hidden;
  }
  .card--front { top: 165px; background: var(--card-white); }
  .card--back {
    top: 653px;
    background: linear-gradient(180deg, var(--back-top), var(--back-bottom));
  }

  .brand {
    position: absolute;
    top: 56px; right: 56px;
    display: flex; align-items: center; gap: 14px;
  }
  .brand__mark {
    width: 30px; height: 30px; border-radius: 4px;
    background: var(--cyan);
  }
  .brand__name {
    font-weight: 600; font-size: 38px; line-height: 1;
    color: var(--navy); letter-spacing: 0.5px;
  }

  .person { position: absolute; left: 49px; top: 228px; }
  .person__name {
    font-weight: 600; font-size: 24px; line-height: 1.1;
    color: var(--cyan); text-transform: uppercase;
  }
  .person__title {
    font-size: 16px; color: var(--ink); margin-top: 2px;
  }
  .divider {
    position: absolute; left: 49px; right: 53px; top: 283px;
    height: 1px; background: var(--rule);
  }
  .contact-list {
    position: absolute; left: 49px; top: 292px;
    list-style: none; font-size: 16.5px; color: var(--ink); line-height: 20.5px;
  }
  .contact-list li { display: flex; align-items: center; gap: 10px; }
  .contact-list svg { width: 14px; height: 14px; flex: none; }
  .address {
    position: absolute; right: 53px; top: 292px;
    font-style: normal; text-align: right;
    font-size: 16.5px; color: var(--ink); line-height: 20.5px;
  }

  .back-brand {
    position: absolute; inset: 0;
    display: flex; align-items: center; justify-content: center; gap: 22px;
  }
  .back-brand__mark {
    width: 56px; height: 56px; border-radius: 8px; background: var(--cyan);
  }
  .back-brand__name {
    font-weight: 600; font-size: 72px; line-height: 1;
    color: var(--cyan); letter-spacing: 1px;
  }
</style>
</head>
<body>
  <section class="card card--front">
    <div class="brand">
      <span class="brand__mark"></span>
      <span class="brand__name">VERODEX</span>
    </div>

    <div class="person">
      <h1 class="person__name">Daniel Moreno</h1>
      <p class="person__title">Managing Director</p>
    </div>

    <div class="divider"></div>

    <ul class="contact-list">
      <li>
        <svg viewBox="0 0 24 24" aria-hidden="true"><path fill="var(--cyan)" d="M6.6 10.8a15.1 15.1 0 0 0 6.6 6.6l2.2-2.2c.3-.3.7-.4 1-.2 1.1.4 2.3.6 3.6.6.6 0 1 .4 1 1V20c0 .6-.4 1-1 1A17 17 0 0 1 3 4c0-.6.4-1 1-1h3.5c.6 0 1 .4 1 1 0 1.3.2 2.5.6 3.6.1.3 0 .7-.2 1z"/></svg>
        555-210-4817
      </li>
      <li>
        <svg viewBox="0 0 24 24" aria-hidden="true"><rect x="6" y="1.5" width="12" height="21" rx="2" fill="none" stroke="var(--cyan)" stroke-width="2"/><circle cx="12" cy="19" r="1.2" fill="var(--cyan)"/></svg>
        555-302-7741
      </li>
      <li>
        <svg viewBox="0 0 24 24" aria-hidden="true"><rect x="2" y="5" width="20" height="14" rx="1.5" fill="var(--cyan)"/><path d="M3 6l9 7 9-7" fill="none" stroke="#fff" stroke-width="1.6"/></svg>
        info@verodex.com
      </li>
    </ul>

    <address class="address">
      1420 Harbor View Road<br>
      Portland, Oregon 97205<br>
      www.verodex.com
    </address>
  </section>

  <section class="card card--back">
    <div class="back-brand">
      <span class="back-brand__mark"></span>
      <span class="back-brand__name">VERODEX</span>
    </div>
  </section>
</body>
</html>
```